Create Website for new company called "Verdale Lodge 37"

Verdale Lodge 37 is a new business situated in Southwestern Colorado. We are creating a business that will rent out spaces where clients can grow their own marijuana. Picture a large green house with partitioned spaces that are secured by a lock. Best way to envision this would be to think of a storage business that rents out storage rooms. The difference is that we will be having the units inside a green house ( for growing purposes) Picture a small area that is secured by locks, Picture an area that has the ability to provide state of the art security, cameras etc. We want to focus our efforts on professionals, blue collar workers and end users of marijuana. Our emphasis is in the area of assisting those whom wish to grow their own plants. We want to provide them a safe facility in which to do that. . Keep in mind that we also build custom grow rooms at clients homes and provide a grow pod (lease these) where a small grow unit will be delivered and picked up from our clients whom want to lease a unit for a short amount of time. We have a business card ( just designed) and will send that information to those whom express an interests in this project. We want to be able to sign people up for our services by entering an agreement and signing the agreement while on the internet. We want to provide our services to those whom consume recreational and medical marijuana. This site will need to gather information I.e email addresses so that we can followup with offers. This is a tremendous opportunity for the right designer. We will be creating many more websites as other states come on line and make marijuana legal to consume. Use the business card model for a point of reference of how we envision the concept. That is a business card we just recently printed. The hands and the plant is our logo so far. Open to suggestions. There will be three levels of service. Bronze, Silver, Gold or Platinum. We will also have a retail biz down the road but not at the present time.

Target Market(s)

Ages 21-60

Industry/Entity Type

Medical

Logo Text

Verdale Lodge 37.

Number of Pages Required

5+ page

Requirements
Must have
• Clean appearance not to busy , easily navigable from link to link, page to page. Must have ability down the road to enter into a contractual agreement via the website. Must use our provided logo and example of that is on our business card that will be uploaded here shortly. We would like to have the colors that are on the business card however if you have suggestions or color schemes that you want us to consider that is okay.
Nice to have
• Nice to have a animation of seed to weed and how clients can save a tremendous amount of money growing their own cannabis. Nice to have testimonial page or feedback page. Have a membership component to website,
Should not have
• No flashing lights, etc. Not to busy in terms of animations.

```html
<!DOCTYPE html>
<html lang="en">
<head>
<meta charset="utf-8">
<title>Verdale Lodge 37</title>
<link rel="stylesheet" href="https://fonts.googleapis.com/css2?family=Oswald:wght@400;500;600&family=Ubuntu:wght@400;500;700&family=Great+Vibes&display=swap">
<style>
:root{
  --green:#0a6b35;
  --green-dark:#075a2c;
  --orange:#c9782a;
  --text:#666;
  --light:#ececec;
  --rule:#e2e2e2;
  --footer:#252525;
  --white:#fff;
}
*{margin:0;padding:0;box-sizing:border-box}
html,body{width:982px;height:1200px;overflow:hidden;background:var(--white)}
body{position:relative;font-family:Arial,Helvetica,sans-serif;color:var(--text)}
.abs{position:absolute}
.top-bar{left:0;top:0;width:982px;height:3px;background:var(--green)}
.brand{left:80px;top:26px;display:flex;align-items:center;gap:8px;font-family:Oswald,sans-serif;font-weight:500;font-size:22px;color:#333;letter-spacing:.3px}
.brand-mark{width:16px;height:16px;border-radius:50%;background:var(--green)}
.nav{left:565px;top:3px;display:flex;font-family:Oswald,sans-serif;font-weight:500;font-size:12px;color:#222}
.nav a{display:block;height:54px;line-height:78px;color:inherit;text-decoration:none;margin-right:33px;text-transform:uppercase}
.nav a.active{background:var(--green);color:var(--white);padding:0 7px;margin-right:22px;line-height:78px}
.nav a:last-child{margin-right:0}
.hero{left:81px;top:79px;width:820px;height:362px;background:radial-gradient(circle at 28% 42%,#e9d6c4 0 16%,transparent 30%),linear-gradient(120deg,#8fbf3a 0%,#b9d75c 40%,#d8e9a6 70%,#9cc93d 100%)}
.hero-title{left:550px;top:193px;font-family:Oswald,sans-serif;font-weight:600;font-size:43px;color:var(--orange);letter-spacing:.5px;text-transform:uppercase;line-height:1}
.hero-rule{left:550px;top:253px;width:277px;height:1px;background:rgba(255,255,255,.8)}
.hero-sub{left:550px;top:266px;font-family:Ubuntu,sans-serif;font-weight:500;font-size:15px;line-height:24px;color:var(--white);text-shadow:0 1px 2px rgba(0,0,0,.35)}
.hero-arrow{top:384px;width:31px;height:31px;background:rgba(10,107,53,.55)}
.hero-arrow svg{display:block;margin:9px auto}
.shadow{height:40px;background:radial-gradient(ellipse at 50% 0%,rgba(0,0,0,.55) 0%,rgba(0,0,0,.15) 45%,transparent 70%)}
.card-img{top:486px;width:260px;height:134px}
.heading{font-family:Oswald,sans-serif;font-weight:500;font-size:15px;color:var(--green);text-transform:uppercase;letter-spacing:-.2px}
.rule{height:4px;background:repeating-linear-gradient(135deg,var(--rule) 0 1px,transparent 1px 3px)}
.copy{font-size:8.6px;line-height:15.5px;color:var(--text);text-align:justify}
.more{font-size:8.6px;color:var(--orange);display:flex;align-items:center;gap:4px}
.quote-box{left:641px;top:830px;width:260px;height:83px;background:var(--light)}
.quote-tail{left:672px;top:913px;width:0;height:0;border-left:0 solid transparent;border-right:14px solid transparent;border-top:12px solid var(--light)}
.avatar{left:656px;top:843px;width:55px;height:55px;border-radius:50%;background:linear-gradient(#d9dfe6,#b8c4cf);border:2px solid var(--white);box-shadow:-2px 2px 0 var(--green)}
.quote{left:736px;top:850px;width:147px;font-size:8.8px;line-height:14px;font-style:italic;color:#9a9a9a;text-align:justify}
.qmark{font-family:Georgia,serif;font-size:26px;color:#c8c8c8;line-height:1}
.signature{left:657px;top:925px;font-family:"Great Vibes",cursive;font-size:17px;color:var(--green)}
.contact-band{left:0;top:998px;width:982px;height:88px;background:#efefef}
.contact{top:1030px;display:flex;gap:8px;align-items:flex-start;font-family:Ubuntu,sans-serif}
.contact b{display:block;font-weight:400;font-size:12.5px;color:#555;text-transform:uppercase;line-height:14px}
.contact span{font-size:9.6px;color:#555}
.footer{left:0;top:1086px;width:982px;height:109px;background:var(--footer)}
.bottom-bar{left:0;top:1195px;width:982px;height:5px;background:var(--green)}
.foot-links{left:81px;top:1122px;font-family:Oswald,sans-serif;font-size:10px;color:#c9c9c9;word-spacing:2px}
.foot-links i{font-style:normal;margin:0 13px}
.foot-copy{left:81px;top:1144px;font-family:Oswald,sans-serif;font-size:10px;color:#c9c9c9}
.social{top:1125px;width:27px;height:27px;background:#f2f2f2}
</style>
</head>
<body>
<div class="abs top-bar"></div>
<div class="abs brand"><span class="brand-mark"></span>VERDALE LODGE 37</div>
<nav class="abs nav">
  <a class="active" href="#">Home</a><a href="#">About Us</a><a href="#">Services</a><a href="#">Clients</a><a href="#">Contact Us</a>
</nav>

<div class="abs hero" role="img" aria-label="Hands holding soil with a young seedling against a soft green background"></div>
<div class="abs hero-title">Verdale Lodge</div>
<div class="abs hero-rule"></div>
<div class="abs hero-sub">Large Green House With Partitioned Spaces<br>That Are Secured By a Lock...</div>
<div class="abs hero-arrow" style="left:800px"><svg width="10" height="13" viewBox="0 0 10 13"><path d="M7 1L2 6.5 7 12" fill="none" stroke="#fff" stroke-width="1.6"/></svg></div>
<div class="abs hero-arrow" style="left:837px"><svg width="10" height="13" viewBox="0 0 10 13"><path d="M3 1l5 5.5L3 12" fill="none" stroke="#fff" stroke-width="1.6"/></svg></div>
<div class="abs shadow" style="left:81px;top:441px;width:820px"></div>

<div class="abs card-img" style="left:81px;background:linear-gradient(#cfe6cf,#58a83c 60%,#2f7a22)" role="img" aria-label="Young plants growing inside a grow tent"></div>
<div class="abs card-img" style="left:361px;background:linear-gradient(#d8d2c8,#6f8b4a 45%,#3b3430)" role="img" aria-label="Potted plants in a small indoor grow room"></div>
<div class="abs card-img" style="left:641px;background:linear-gradient(#e6e6e2,#6c8f4c 35%,#3f6a2a)" role="img" aria-label="Dense plants under lights in a large grow space"></div>
<div class="abs shadow" style="left:101px;top:620px;width:220px;height:14px"></div>
<div class="abs shadow" style="left:381px;top:620px;width:220px;height:14px"></div>
<div class="abs shadow" style="left:661px;top:620px;width:220px;height:14px"></div>

<div class="abs heading" style="left:79px;top:637px">Rent Out Spaces</div>
<div class="abs rule" style="left:81px;top:660px;width:260px"></div>
<p class="abs copy" style="left:81px;top:677px;width:254px">Lorem ipsum dolor sit amet, consectetuer adipiscing elit. Aenean commodo ligula eget dolor. Aenean massa.Cum sociis natoque penatibus et magnis dis parturient montes</p>
<div class="abs more" style="left:81px;top:732px">Read More <svg width="7" height="7" viewBox="0 0 7 7"><path d="M1 1l2.5 2.5L1 6M3.5 1L6 3.5 3.5 6" fill="none" stroke="currentColor"/></svg></div>

<div class="abs heading" style="left:359px;top:637px">Secured By a Lock</div>
<div class="abs rule" style="left:361px;top:660px;width:260px"></div>
<p class="abs copy" style="left:359px;top:673px;width:254px">Lorem ipsum dolor sit amet, consectetuer adipiscing elit. Aenean commodo ligula eget dolor. Aenean massa.Cum sociis natoque penatibus et magnis dis parturient montes</p>
<div class="abs more" style="left:359px;top:728px">Read More <svg width="7" height="7" viewBox="0 0 7 7"><path d="M1 1l2.5 2.5L1 6M3.5 1L6 3.5 3.5 6" fill="none" stroke="currentColor"/></svg></div>

<div class="abs heading" style="left:640px;top:638px">Verdale Lodge</div>
<div class="abs rule" style="left:641px;top:660px;width:260px"></div>
<p class="abs copy" style="left:641px;top:673px;width:254px">Lorem ipsum dolor sit amet, consectetuer adipiscing elit. Aenean commodo ligula eget dolor. Aenean massa.Cum sociis natoque penatibus et magnis dis parturient montes</p>
<div class="abs more" style="left:641px;top:728px">Read More <svg width="7" height="7" viewBox="0 0 7 7"><path d="M1 1l2.5 2.5L1 6M3.5 1L6 3.5 3.5 6" fill="none" stroke="currentColor"/></svg></div>

<div class="abs heading" style="left:79px;top:779px">Welcome to Verdale Lodge</div>
<div class="abs rule" style="left:81px;top:807px;width:532px"></div>
<div class="abs" style="left:81px;top:830px;width:190px;height:118px;background:radial-gradient(circle at 55% 50%,#9cc85a,#6ea23a 60%,#b9d690)" role="img" aria-label="Close-up of a green cannabis leaf"></div>
<div class="abs shadow" style="left:91px;top:948px;width:170px;height:14px"></div>
<p class="abs copy" style="left:285px;top:826px;width:328px;line-height:16.8px">Lorem ipsum dolor sit amet, consectetuer adipiscing elit. Aenean commodo ligula eget dolor. Aenean massa. Cum sociis natoque penatibus et magnis dis parturient montes, nascetur ridiculus mus. Donec quam felis, ultricies nec, pellentesque eu, pretium quis, sem. Nulla consequat massa quis enim. Donec pede justo, fringilla vel, aliquet nec, vulputate eget, arcu. In enim justo, rhoncus ut, imperdiet a, venenatis vitae, justo. Nullam dictum felis eu pede mollis pretium. Integer tincidunt.</p>
<div class="abs more" style="left:285px;top:940px">Read More <svg width="7" height="7" viewBox="0 0 7 7"><path d="M1 1l2.5 2.5L1 6M3.5 1L6 3.5 3.5 6" fill="none" stroke="currentColor"/></svg></div>

<div class="abs heading" style="left:641px;top:779px">What Our Client Says</div>
<div class="abs rule" style="left:641px;top:807px;width:260px"></div>
<div class="abs quote-box"></div>
<div class="abs quote-tail"></div>
<div class="abs avatar" role="img" aria-label="Client portrait"></div>
<div class="abs qmark" style="left:716px;top:842px">&ldquo;</div>
<p class="abs quote">Lorem ipsum dolor sit amet, consectetuer adipiscing elit. Aenean commodo ligula eget dolor</p>
<div class="abs qmark" style="left:846px;top:876px">&rdquo;</div>
<div class="abs signature">Mara Lind</div>

<div class="abs contact-band"></div>
<div class="abs contact" style="left:180px">
  <svg width="25" height="22" viewBox="0 0 25 22"><path d="M2 8c0-5 21-5 21 0l-4 1-1-3H7L6 9z" fill="var(--green)"/><path d="M6 10h13l3 11H3z" fill="var(--green)"/><circle cx="12.5" cy="15" r="3" fill="#efefef"/></svg>
  <div><b>Phone</b><span>080 0412 5530</span></div>
</div>
<div class="abs contact" style="left:335px">
  <svg width="25" height="22" viewBox="0 0 25 22"><rect x="6" y="1" width="13" height="6" fill="var(--green)"/><rect x="1" y="7" width="23" height="9" rx="2" fill="var(--green)"/><rect x="6" y="13" width="13" height="8" fill="#efefef" stroke="var(--green)" stroke-width="2"/></svg>
  <div><b>Fax</b><span>08) 8411 7294</span></div>
</div>
<div class="abs contact" style="left:475px">
  <svg width="26" height="26" viewBox="0 0 26 26"><circle cx="13" cy="13" r="11.5" fill="none" stroke="var(--green)" stroke-width="2"/><path d="M9 7l3 3-2 2c1 2 2 3 4 4l2-2 3 3-2 2c-5 0-10-5-10-10z" fill="var(--green)"/></svg>
  <div><b>Mobile</b><span>0408 327 916</span></div>
</div>
<div class="abs contact" style="left:637px">
  <svg width="28" height="20" viewBox="0 0 28 20"><rect x="1" y="2" width="26" height="17" fill="var(--green)"/><path d="M1 2l13 10L27 2M1 19l10-8M27 19l-10-8" fill="none" stroke="#efefef" stroke-width="1.5"/></svg>
  <div><b>Email</b><span>Info @verdalelodge37.com</span></div>
</div>

<div class="abs footer"></div>
<div class="abs foot-links">Home<i>/</i>About Us<i>/</i>Services<i>/</i>Clients<i>/</i>Contact Us</div>
<div class="abs foot-copy">Copy right &copy; 2014 &nbsp;verdalelodge37 &nbsp;| &nbsp; Privacy Policy</div>
<div class="abs social" style="left:766px"></div>
<div class="abs social" style="left:802px"></div>
<div class="abs social" style="left:838px"></div>
<div class="abs social" style="left:874px"></div>
<div class="abs bottom-bar"></div>
</body>
</html>
```